Every Shelf Set Neatly or ESN Organized needs a business card design. ESN Organized is a professi

We need a business card design that is clean, sharp and conveys a sense of organization. I already have a logo.

Target Market(s)

Families (specifically mothers), small business owners, parents, seniors

Industry/Entity Type

Business

Contact Information for Business Card

My website is www.esnorganized-example.com and my sociallink page is http://www.sociallink-example.com/everyshelfsetneatly. The phone number is 418-552-7094 and I want to be listed as Lorna M. Pelham, Owner

Requirements
Must have
• My logo.

```html
<!DOCTYPE html>
<html lang="en">
<head>
<meta charset="utf-8">
<title>ESN Organized – Business Card</title>
<link href="https://fonts.googleapis.com/css2?family=Montserrat:wght@200;300;400&family=Open+Sans:wght@400;600;700&display=swap" rel="stylesheet">
<style>
  :root {
    --backdrop: #141414;
    --brand-blue: #0a74d8;
    --card-white: #ffffff;
    --ink-grey: #3a3a3a;
    --on-blue: #ffffff;
  }
  * { margin: 0; padding: 0; box-sizing: border-box; }
  html, body {
    width: 1200px; height: 900px; overflow: hidden;
    background: var(--backdrop);
  }
  .canvas { position: relative; width: 1200px; height: 900px; }
  .card {
    position: absolute; top: 318px; width: 440px; height: 270px;
    text-align: center;
  }
  .card-front { left: 168px; background: var(--card-white); }
  .card-back { left: 627px; background: var(--brand-blue); color: var(--on-blue); }

  .owner-name {
    position: absolute; top: 27px; left: 0; right: 0;
    font: 700 16px/1 "Open Sans", sans-serif; color: var(--brand-blue);
  }
  .owner-role {
    position: absolute; top: 52px; left: 0; right: 0;
    font: 400 12px/1 "Open Sans", sans-serif; color: var(--ink-grey);
  }
  .brand-name {
    position: absolute; left: 0; right: 0;
    font-family: "Montserrat", sans-serif; font-weight: 300; line-height: 1;
  }
  .card-front .brand-name { top: 80px; font-size: 100px; color: var(--brand-blue); }
  .card-back .brand-name { top: 58px; font-size: 74px; color: var(--on-blue); }

  .contact-list {
    position: absolute; top: 193px; left: 0; right: 0; list-style: none;
    font: 400 12px/16.5px "Open Sans", sans-serif; color: var(--ink-grey);
  }
  .tagline-top {
    position: absolute; top: 145px; left: 0; right: 0;
    font: 400 14px/1 "Montserrat", sans-serif; letter-spacing: 2.5px;
  }
  .tagline-main {
    position: absolute; top: 165px; left: 0; right: 0;
    font: 400 23px/1 "Montserrat", sans-serif; letter-spacing: 5px;
  }
  .social-link {
    position: absolute; top: 216px; left: 0; right: 0;
    font: 600 14px/1 "Open Sans", sans-serif;
  }
</style>
</head>
<body>
<main class="canvas">
  <section class="card card-front">
    <h1 class="owner-name">LORNA M. PELHAM</h1>
    <p class="owner-role">Owner</p>
    <div class="brand-name">ESN</div>
    <ul class="contact-list">
      <li>418-552-7094</li>
      <li>info@esnorganized-example.com</li>
      <li>www.esnorganized-example.com</li>
    </ul>
  </section>
  <section class="card card-back">
    <div class="brand-name">ESN</div>
    <p class="tagline-top">Every Shelf Set Neatly</p>
    <p class="tagline-main">ORGANIZED</p>
    <p class="social-link">sociallink/everyshelfsetneatly</p>
  </section>
</main>
</body>
</html>
```